Tandem Hearth Works Pty Ltd

We need business cards for a company based in Perth, we install, service and maintain fire equipment.
On the front we want a great design with our logo and a small spot for our full company name, general company email address and office number. On the back we need space for our name, title, mobile number and email address on the back.

Target Market(s)

Facility managers and commercial/industrial building owners/occupiers.

Contact Information for Business Card

Font styles to use
Sans Serif

Requirements
Must have
• Please only submit 5 of your best samples.
Darker tones are preferred.
Nice to have
• We want to use, black, red and grey. Keep it modern and clean.
I've attached the company logo and a sample of a boarder we use on our emergency plans.
Should not have
• No preference. Let the designer choose.

```html
<!DOCTYPE html>
<html lang="en">
<head>
<meta charset="utf-8">
<title>Tandem Hearth Works – Business Card</title>
<link rel="stylesheet" href="https://fonts.googleapis.com/css2?family=Archivo:wght@400;500;700&display=swap">
<style>
  :root {
    --canvas: #d6d6d6;
    --red: #ed1c24;
    --red-light: #f4293a;
    --white: #ffffff;
    --ink: #1f1f1f;
    --accent: #f7a35c;
  }
  * { box-sizing: border-box; margin: 0; padding: 0; }
  html, body { width: 1200px; height: 800px; overflow: hidden; }
  body {
    background: var(--canvas);
    font-family: "Archivo", Arial, sans-serif;
    position: relative;
  }
  .card {
    position: absolute;
    top: 246px;
    width: 540px;
    height: 308px;
    overflow: hidden;
    box-shadow: 0 3px 8px rgba(0,0,0,.18);
  }
  .card--front {
    left: 40px;
    background: radial-gradient(circle at 40% 45%, var(--red-light), var(--red) 70%);
    color: var(--white);
  }
  .card--back {
    left: 620px;
    background: var(--white);
    color: var(--ink);
  }

  /* front */
  .stripe {
    position: absolute;
    height: 10px;
    background: var(--white);
  }
  .stripe--top { left: 0; top: 24px; width: 230px; }
  .stripe--bottom { right: 0; bottom: 24px; width: 150px; }

  .brand {
    position: absolute;
    left: 0; right: 0;
    top: 78px;
    display: flex;
    flex-direction: column;
    align-items: center;
  }
  .brand__logo {
    display: flex;
    align-items: center;
    gap: 12px;
  }
  .brand__square {
    width: 30px;
    height: 30px;
    background: var(--white);
  }
  .brand__wordmark {
    font-size: 40px;
    font-weight: 500;
    line-height: 1;
  }
  .brand__name {
    margin-top: 18px;
    font-size: 23px;
    font-weight: 500;
  }
  .brand__web {
    margin-top: 6px;
    display: flex;
    align-items: center;
    gap: 12px;
    font-size: 14px;
    letter-spacing: .3px;
  }
  .rule {
    display: block;
    width: 70px;
    height: 1px;
  }
  .rule--left { background: linear-gradient(90deg, var(--accent), var(--white)); }
  .rule--right { background: linear-gradient(90deg, var(--white), var(--accent)); }
  .brand__phone {
    margin-top: 6px;
    font-size: 14px;
    display: flex;
    align-items: center;
    gap: 5px;
  }

  /* back */
  .person {
    position: absolute;
    left: 0; right: 0; top: 98px;
    text-align: center;
  }
  .person__name {
    font-size: 30px;
    font-weight: 700;
    letter-spacing: .5px;
  }
  .person__title {
    font-size: 13px;
    margin-top: 2px;
  }
  .contact {
    position: absolute;
    left: 0; right: 0; top: 188px;
    text-align: center;
    font-size: 15px;
    line-height: 1.25;
  }
  .contact__icons {
    display: flex;
    justify-content: center;
    gap: 6px;
    margin-bottom: 6px;
  }
</style>
</head>
<body>

<section class="card card--front" aria-label="Card front">
  <div class="stripe stripe--top"></div>
  <div class="stripe stripe--bottom"></div>
  <div class="brand">
    <div class="brand__logo">
      <span class="brand__square" aria-hidden="true"></span>
      <span class="brand__wordmark">Tandem Hearth Works</span>
    </div>
    <div class="brand__name">Tandem Hearth Works Pty Ltd</div>
    <div class="brand__web">
      <span class="rule rule--left"></span>
      <span>www.tandemhearthworks.com</span>
      <span class="rule rule--right"></span>
    </div>
    <div class="brand__phone">
      <svg width="14" height="14" viewBox="0 0 14 14" aria-hidden="true">
        <circle cx="7" cy="7" r="6" fill="none" stroke="#fff" stroke-width="1.4"/>
        <path d="M5 4.2c.4-.3.8-.2 1 .2l.4.8c.1.3 0 .5-.2.7l-.3.2c.3.7.8 1.2 1.5 1.5l.2-.3c.2-.2.4-.3.7-.2l.8.4c.4.2.5.6.2 1-.5.6-1.1.8-1.8.5C6.2 8.4 5.4 7.6 4.8 6.3c-.3-.7-.2-1.4.2-2.1z" fill="#fff"/>
      </svg>
      <span>+0198765432</span>
    </div>
  </div>
</section>

<section class="card card--back" aria-label="Card back">
  <div class="person">
    <div class="person__name">Daniel Harper</div>
    <div class="person__title">Manager</div>
  </div>
  <div class="contact">
    <div class="contact__icons">
      <svg width="20" height="20" viewBox="0 0 20 20" aria-hidden="true">
        <circle cx="10" cy="10" r="10" fill="#1f1f1f"/>
        <path d="M7 5.5c.5-.4 1-.3 1.3.2l.6 1.1c.2.4.1.7-.2 1l-.4.3c.4.9 1.1 1.6 2 2l.3-.4c.3-.3.6-.4 1-.2l1.1.6c.5.3.6.8.2 1.3-.7.8-1.5 1-2.4.6C8.8 11.3 7.8 10.3 7 8.6c-.4-.9-.3-2 .4-2.9z" fill="#fff"/>
      </svg>
      <svg width="20" height="20" viewBox="0 0 20 20" aria-hidden="true">
        <circle cx="10" cy="10" r="10" fill="#1f1f1f"/>
        <rect x="5" y="6.5" width="10" height="7" fill="none" stroke="#fff" stroke-width="1.2"/>
        <path d="M5 6.5l5 4 5-4" fill="none" stroke="#fff" stroke-width="1.2"/>
      </svg>
    </div>
    <div>+1 555 014 270</div>
    <div>danielharper@thw.com</div>
  </div>
</section>

</body>
</html>
```